Pay-Per-Use Production Space Warehouse/Factory/Production Space

Please refer to project requirements as attached/included. This is an introductory marketing Info graphic to capture attention or create awareness to a new, epic and unique business value preposition and business model for customer to easily launch new products/services and robust supply chain. This is a win win revolutionary business solution compare with traditional or conventional methods of outsourcing or DIY design, build, finance, operate and maintain. PROJECT Requirement to info graphic designer
1) Subject to confidentiality and all rights reserved
2) Below are some photos which you may consider to use for this work
3) Clarify and verify with us if there are any questions related to this work and design

Target Market(s)

Global, (Life sciences, food, others)

Industry/Entity Type

Medical And Science

Requirements
Must have
• Dynamic background template.
Should not have
• Monotonous and un-creative designs

```html
<!DOCTYPE html>
<html lang="en">
<head>
<meta charset="utf-8">
<title>Pay-Per-Use Applicable to All</title>
<link href="https://fonts.googleapis.com/css2?family=Montserrat:wght@400;600;700;800&display=swap" rel="stylesheet">
<style>
  :root {
    --slate: #58595b;
    --blue: #124f80;
    --teal: #3bbba8;
    --orange: #f2a71e;
    --red: #d63527;
    --charcoal: #313b3f;
    --caption: #4d4d4f;
    --rule: #a7a9ac;
    --white: #ffffff;
    --paper: #ffffff;
  }
  * { box-sizing: border-box; margin: 0; padding: 0; }
  html, body { width: 848px; height: 1200px; overflow: hidden; background: var(--paper); }
  body { font-family: "Montserrat", sans-serif; }
  .poster { position: relative; width: 848px; height: 1200px; overflow: hidden; background: var(--paper); }

  .header-band {
    position: absolute; left: 79px; top: 0; width: 697px; height: 229px;
    background: var(--slate); color: var(--white); text-align: center;
  }
  .title-top { position: absolute; left: 0; right: 0; top: 100px; font-size: 42px; font-weight: 800; letter-spacing: 0.5px; line-height: 1; }
  .title-main { position: absolute; left: 0; right: 0; top: 150px; font-size: 53px; font-weight: 800; letter-spacing: 1px; line-height: 1; }

  .color-strip { position: absolute; top: 232px; height: 5px; }
  .color-strip::after { content: ""; position: absolute; left: -12px; top: 5px; width: 100%; height: 4px; background: #e6e7e8; }
  .strip-blue { left: 128px; width: 107px; background: var(--blue); }
  .strip-teal { left: 250px; width: 107px; background: var(--teal); }
  .strip-orange { left: 372px; width: 108px; background: var(--orange); }
  .strip-red { left: 497px; width: 108px; background: var(--red); }
  .strip-charcoal { left: 619px; width: 108px; background: var(--charcoal); }

  .arrows { position: absolute; left: 0; top: 0; width: 848px; height: 1200px; }

  .segment { position: absolute; width: 97px; text-align: center; }
  .segment-photo { width: 96px; height: 96px; border: 1px solid #d1d3d4; }
  .segment-rule { width: 97px; height: 4px; background: var(--rule); margin-top: 5px; }
  .segment-label { position: absolute; left: -60px; right: -60px; top: 112px; font-size: 13.5px; font-weight: 700; letter-spacing: 0.6px; color: var(--caption); line-height: 17px; }

  .seg-startups { left: 94px; top: 348px; }
  .seg-startups .segment-photo { background: linear-gradient(160deg, #e8e6e2, #a9a8a4 60%, #7f7e7a); }
  .seg-multinational { left: 661px; top: 348px; }
  .seg-multinational .segment-photo { background: linear-gradient(180deg, #4a68a8 0%, #9fb2d6 45%, #8c8f8c 62%, #5d7a3c 100%); }
  .seg-sme { left: 142px; top: 522px; }
  .seg-sme .segment-photo { background: linear-gradient(140deg, #4e5150, #bfc0ba 50%, #6f6f68); }
  .seg-others { left: 615px; top: 522px; }
  .seg-others .segment-photo { background: linear-gradient(160deg, #6b716f, #c9cfcb 50%, #8a4a44 75%, #b4b8b4); }

  .value-band {
    position: absolute; left: 79px; top: 713px; width: 697px; height: 487px;
    background: var(--slate); color: var(--white); text-align: center;
  }
  .value-copy { position: absolute; left: 0; right: 0; top: 54px; font-size: 14px; line-height: 17px; font-weight: 400; letter-spacing: 0.3px; }
  .value-copy h2 { font-size: 16.5px; font-weight: 700; line-height: 20px; letter-spacing: 0.2px; }
  .value-copy p { margin-bottom: 17px; }
  .value-copy strong { font-weight: 600; letter-spacing: 0.8px; }

  .benefits { position: absolute; left: 0; top: 256px; width: 697px; height: 120px; }
  .benefit { position: absolute; width: 100px; text-align: center; }
  .benefit-icon { width: 74px; height: 74px; border-radius: 50%; margin: 0 auto; display: flex; align-items: center; justify-content: center; box-shadow: 0 8px 0 -2px rgba(0,0,0,0.18); }
  .benefit-label { margin-top: 24px; font-size: 14px; font-weight: 400; letter-spacing: 1px; }
  .b-cheaper { left: 122px; } .b-cheaper .benefit-icon { background: radial-gradient(circle at 35% 30%, #1d6aa6, var(--blue) 60%, #0b3558); }
  .b-better { left: 238px; } .b-better .benefit-icon { background: radial-gradient(circle at 35% 30%, #55d1be, var(--teal) 60%, #1f7a6c); }
  .b-faster { left: 364px; } .b-faster .benefit-icon { background: radial-gradient(circle at 35% 30%, #ffc24a, var(--orange) 60%, #a86c0c); }
  .b-assured { left: 481px; } .b-assured .benefit-icon { background: radial-gradient(circle at 35% 30%, #ee5a49, var(--red) 60%, #8e1f15); }

  .divider { position: absolute; top: 350px; width: 1.5px; height: 22px; }
  .d-teal { left: 227px; background: var(--teal); }
  .d-orange { left: 349px; background: var(--orange); }
  .d-red { left: 470px; background: var(--red); }

  .footnote { position: absolute; left: 0; right: 0; top: 418px; font-size: 12px; letter-spacing: 0.3px; }
</style>
</head>
<body>
<div class="poster">

  <header class="header-band">
    <div class="title-top">PAY-PER-USE</div>
    <h1 class="title-main">APPLICABLE TO ALL</h1>
  </header>

  <div class="color-strip strip-blue"></div>
  <div class="color-strip strip-teal"></div>
  <div class="color-strip strip-orange"></div>
  <div class="color-strip strip-red"></div>
  <div class="color-strip strip-charcoal"></div>

  <svg class="arrows" viewBox="0 0 848 1200" aria-hidden="true">
    <defs>
      <filter id="arrow-shadow" x="-20%" y="-20%" width="140%" height="140%">
        <feDropShadow dx="-6" dy="10" stdDeviation="8" flood-color="#000" flood-opacity="0.16"/>
      </filter>
    </defs>
    <g transform="scale(0.6833)" fill="none" stroke-width="32" stroke-linejoin="miter" filter="url(#arrow-shadow)">
      <g stroke="var(--blue)">
        <path d="M623 385 V500 C623 625 505 668 440 655 C405 648 375 636 345 622"/>
        <polyline points="410,592 322,614 357,696"/>
      </g>
      <g stroke="var(--teal)">
        <path d="M632 575 C585 680 505 765 415 832"/>
        <polyline points="410,748 390,845 485,858"/>
      </g>
      <g stroke="var(--orange)">
        <path d="M624 560 V950"/>
        <polyline points="564,885 624,952 684,885"/>
      </g>
      <g stroke="var(--red)">
        <path d="M648 550 C680 665 750 762 840 832"/>
        <polyline points="832,748 858,848 765,860"/>
      </g>
      <g stroke="var(--charcoal)">
        <path d="M665 568 C720 660 835 682 910 622"/>
        <polyline points="838,588 932,608 894,695"/>
      </g>
    </g>
  </svg>

  <div class="segment seg-startups">
    <div class="segment-photo" role="img" aria-label="Photo of a compact start-up production room with stainless process equipment"></div>
    <div class="segment-rule"></div>
    <div class="segment-label">START UPS</div>
  </div>

  <div class="segment seg-multinational">
    <div class="segment-photo" role="img" aria-label="Rendering of a large modern factory building with parking"></div>
    <div class="segment-rule"></div>
    <div class="segment-label">MULTINATIONAL<br>CORPORATIONS</div>
  </div>

  <div class="segment seg-sme">
    <div class="segment-photo" role="img" aria-label="Aerial rendering of a mid-size production floor layout"></div>
    <div class="segment-rule"></div>
    <div class="segment-label">SMALL MEDIUM<br>ENTERPRISES</div>
  </div>

  <div class="segment seg-others">
    <div class="segment-photo" role="img" aria-label="Rendering of a modular cleanroom space seen from above"></div>
    <div class="segment-rule"></div>
    <div class="segment-label">OTHERS</div>
  </div>

  <section class="value-band">
    <div class="value-copy">
      <h2>Value Propositions**:</h2>
      <p>Maximum Technical and Financial Flexibility to<br>Scale Up or Down with Ease. This will allow you to Mitigate Risks,<br>Change Swiftly and to Engage Success Better</p>
      <p>If Apply &amp; Use Continuously, its Gives Your Organization<br><strong>NEW STRATEGIC OPTION</strong></p>
      <p>to Gain the Competitive Advantage to Launch New Products/<br>Services and or Robust Supply Chain</p>
    </div>

    <div class="benefits">
      <div class="benefit b-cheaper">
        <div class="benefit-icon">
          <svg width="42" height="42" viewBox="0 0 42 42" aria-hidden="true">
            <g transform="rotate(-20 21 24)">
              <rect x="9" y="17" width="26" height="16" rx="2" fill="#fff"/>
              <circle cx="22" cy="25" r="5" fill="var(--blue)"/>
              <text x="22" y="28.5" font-family="Montserrat, sans-serif" font-size="8" font-weight="700" fill="#fff" text-anchor="middle">$</text>
            </g>
            <g stroke="#fff" stroke-width="2" fill="none">
              <circle cx="8" cy="8" r="3.5"/><circle cx="8" cy="17" r="3.5"/>
              <path d="M11 9 L22 16 M11 16 L22 9"/>
            </g>
          </svg>
        </div>
        <div class="benefit-label">CHEAPER</div>
      </div>
      <div class="benefit b-better">
        <div class="benefit-icon">
          <svg width="40" height="44" viewBox="0 0 40 44" aria-hidden="true">
            <path d="M13 24 L8 40 L14 37 L17 42 L20 28 M27 24 L32 40 L26 37 L23 42 L20 28" fill="#fff"/>
            <circle cx="20" cy="16" r="13" fill="#fff"/>
            <circle cx="20" cy="16" r="9" fill="var(--teal)"/>
            <polygon points="20,10 21.8,14 26,14.3 22.8,17 23.8,21.2 20,19 16.2,21.2 17.2,17 14,14.3 18.2,14" fill="#fff"/>
          </svg>
        </div>
        <div class="benefit-label">BETTER</div>
      </div>
      <div class="benefit b-faster">
        <div class="benefit-icon">
          <svg width="48" height="42" viewBox="0 0 48 42" aria-hidden="true">
            <g stroke="#fff" stroke-width="2.5" fill="none" stroke-linecap="round">
              <circle cx="29" cy="23" r="13"/>
              <path d="M29 6 V10 M25 5 H33 M29 23 V16 M29 23 L25 27"/>
              <path d="M4 18 H13 M2 24 H12 M5 30 H14"/>
            </g>
          </svg>
        </div>
        <div class="benefit-label">FASTER</div>
      </div>
      <div class="benefit b-assured">
        <div class="benefit-icon">
          <svg width="42" height="40" viewBox="0 0 42 40" aria-hidden="true">
            <rect x="5" y="10" width="26" height="24" fill="none" stroke="#fff" stroke-width="3.5"/>
            <path d="M11 20 L18 28 L37 6" fill="none" stroke="#fff" stroke-width="5" stroke-linecap="square"/>
          </svg>
        </div>
        <div class="benefit-label">ASSURED</div>
      </div>
    </div>

    <span class="divider d-teal"></span>
    <span class="divider d-orange"></span>
    <span class="divider d-red"></span>

    <p class="footnote">**Contact us for more details, case by case basis</p>
  </section>

</div>
</body>
</html>
```